KLV Plant Services

We are a heavy diesel mechanical business with additional air con certificates, remapping engine rebuilt

Contact Information for Business Card

Company Name, Director Name, Managing Director, Contact details, email and website

Font styles to use
Serif
Script

```html
<!DOCTYPE html>
<html lang="en">
<head>
<meta charset="utf-8">
<title>KLV Plant Services – Business Card</title>
<link rel="stylesheet" href="https://fonts.googleapis.com/css2?family=Josefin+Sans:wght@400;600;700&display=swap">
<style>
  :root {
    --navy: #1f1c5c;
    --navy-deep: #15124a;
    --navy-soft: #2e2b6e;
    --ink: #1a1a1a;
    --text: #3a3a3a;
    --rule: #8d8bb0;
    --paper: #ffffff;
    --backdrop: #e9e6e1;
    --watermark-light: #dedede;
  }
  * { box-sizing: border-box; margin: 0; padding: 0; }
  html, body { width: 1200px; height: 900px; overflow: hidden; }
  body {
    background: var(--backdrop);
    font-family: "Josefin Sans", sans-serif;
    position: relative;
  }
  .card {
    position: absolute;
    left: 240px;
    width: 720px;
    height: 411px;
    border-radius: 34px;
    overflow: hidden;
    box-shadow: 0 6px 18px rgba(0,0,0,0.18);
  }
  .card--back { top: 30px; background: var(--navy); }
  .card--front { top: 459px; background: var(--paper); }

  .watermark {
    position: absolute;
    left: 130px;
    top: 120px;
    width: 170px;
    height: 291px;
    border-radius: 18px 18px 0 0;
  }
  .card--back .watermark { background: linear-gradient(180deg, rgba(255,255,255,0.04), rgba(255,255,255,0.1)); }
  .card--front .watermark { left: 150px; top: 90px; background: linear-gradient(180deg, rgba(0,0,0,0.03), rgba(0,0,0,0.09)); }

  .brand {
    position: absolute;
    display: flex;
    align-items: center;
    gap: 14px;
  }
  .brand__mark { width: 26px; height: 26px; border-radius: 50%; }
  .brand__name {
    font-weight: 700;
    font-size: 44px;
    line-height: 1;
    letter-spacing: 0.5px;
  }
  .card--back .brand { left: 330px; top: 120px; }
  .card--back .brand__mark { background: var(--navy-deep); }
  .card--back .brand__name { color: var(--navy-deep); }
  .card--front .brand { left: 330px; top: 80px; }
  .card--front .brand__mark { background: var(--navy); }
  .card--front .brand__name { color: var(--navy); }

  .contact {
    position: absolute;
    left: 58px;
    right: 58px;
    bottom: 34px;
    color: var(--text);
  }
  .contact__rule { height: 1px; background: var(--rule); }
  .contact__rule--top { margin-bottom: 22px; margin-left: 140px; }
  .contact__rule--mid { margin: 12px 0 12px; }
  .contact__name {
    font-size: 22px;
    font-weight: 700;
    color: var(--navy);
    letter-spacing: 1px;
  }
  .contact__title { font-size: 16px; color: var(--text); font-weight: 400; letter-spacing: 0.5px; }
  .contact__sep { color: var(--navy); font-weight: 700; padding: 0 6px; }
  .contact__address { font-size: 15px; margin-top: 8px; letter-spacing: 0.3px; }
  .contact__details { font-size: 13.5px; letter-spacing: 0.3px; white-space: nowrap; }
</style>
</head>
<body>
  <section class="card card--back" aria-label="Card back">
    <div class="watermark" role="img" aria-label="Faint excavator arm decoration"></div>
    <div class="brand">
      <span class="brand__mark"></span>
      <span class="brand__name">KLV Plant Services</span>
    </div>
  </section>

  <section class="card card--front" aria-label="Card front">
    <div class="watermark" role="img" aria-label="Faint excavator arm decoration"></div>
    <div class="brand">
      <span class="brand__mark"></span>
      <span class="brand__name">KLV Plant Services</span>
    </div>
    <div class="contact">
      <div class="contact__rule contact__rule--top"></div>
      <p class="contact__name">DEAN MARLOW<span class="contact__sep">|</span><span class="contact__title">Managing Director</span></p>
      <p class="contact__address">48 Harlow Street, Ridgefield, WA 6102, Australia</p>
      <div class="contact__rule contact__rule--mid"></div>
      <p class="contact__details">T. 0412 555 019<span class="contact__sep">|</span>E. admin@klvplantservices.net<span class="contact__sep">|</span>W. www.klvplantservices.net</p>
    </div>
  </section>
</body>
</html>
```